Tavrelle Capital LLC

Need Professional Business cards for New Investment Fund

Target Market(s)

High Quality investors

Industry/Entity Type

Financial

Contact Information for Business Card

Phone Number +1 555 284 6190
Name Lukas Varenko
Title Fund Manager
email lv@FundTavrelle.com
Website www.FundTavrelle.com

Colors

Designer to choose colors to be used in the design.

Requirements
Must have
• Must have our Logo and all of the above. Must be made so lettering and loge can be raised

```html
<!DOCTYPE html>
<html lang="en">
<head>
<meta charset="utf-8">
<title>Tavrelle Capital LLC – Business Card</title>
<link href="https://fonts.googleapis.com/css2?family=Raleway:wght@400;600&family=Teko:wght@500&display=swap" rel="stylesheet">
<style>
  :root {
    --stage: #1b1b1b;
    --card: #434d42;
    --green: #59bb47;
    --white: #ffffff;
  }
  * { box-sizing: border-box; margin: 0; padding: 0; }
  html, body { width: 1200px; height: 900px; overflow: hidden; background: var(--stage); }
  .canvas { position: relative; width: 1200px; height: 900px; }
  .card {
    position: absolute; left: 250px; width: 700px; height: 400px;
    background: var(--card); overflow: hidden;
  }
  .card-back { top: 35px; }
  .card-front { top: 465px; }

  .brand {
    display: flex; align-items: center; gap: 14px;
    font-family: "Raleway", sans-serif; font-weight: 600;
    color: var(--white); letter-spacing: 2px; white-space: nowrap;
  }
  .brand-dot { width: 22px; height: 22px; border-radius: 50%; background: var(--green); flex: none; }

  .card-back .brand {
    position: absolute; left: 0; right: 0; top: 165px;
    justify-content: center; font-size: 46px;
  }
  .back-bar {
    position: absolute; bottom: 0; left: 270px; width: 260px; height: 12px;
    background: var(--green);
  }

  .card-front .brand { position: absolute; left: 55px; top: 90px; font-size: 40px; }

  .contact {
    position: absolute; right: 55px; top: 140px; text-align: right;
    font-family: "Raleway", sans-serif; color: var(--white);
  }
  .contact-name {
    font-family: "Teko", sans-serif; font-weight: 500; font-size: 38px;
    line-height: 1; color: var(--green); text-transform: uppercase; letter-spacing: 0.5px;
  }
  .contact-title { font-size: 18px; margin-top: 4px; letter-spacing: 0.5px; }
  .contact-list { list-style: none; margin-top: 22px; }
  .contact-list li {
    display: flex; justify-content: flex-end; align-items: center; gap: 14px;
    font-size: 19px; line-height: 30px; letter-spacing: 0.5px; white-space: nowrap;
  }
  .contact-list svg { width: 16px; height: 16px; flex: none; }

  .wave { position: absolute; left: 0; bottom: 0; width: 700px; height: 400px; }
</style>
</head>
<body>
<main class="canvas">
  <section class="card card-back" aria-label="Card back">
    <div class="brand"><span class="brand-dot"></span>Tavrelle</div>
    <div class="back-bar"></div>
  </section>

  <section class="card card-front" aria-label="Card front">
    <svg class="wave" viewBox="0 0 700 400" aria-hidden="true">
      <path d="M0 255 C 150 320, 330 340, 700 325 L 700 400 L 0 400 Z" fill="var(--white)"/>
      <path d="M0 265 C 150 330, 330 348, 700 331 L 700 400 L 0 400 Z" fill="var(--card)"/>
      <path d="M0 275 C 140 338, 330 352, 700 334 L 700 400 L 0 400 Z" fill="var(--white)"/>
      <path d="M0 295 C 150 348, 330 358, 700 345 L 700 400 L 0 400 Z" fill="var(--green)"/>
    </svg>

    <div class="brand"><span class="brand-dot"></span>Tavrelle</div>

    <div class="contact">
      <p class="contact-name">Lukas Varenko</p>
      <p class="contact-title">Title Fund Manager</p>
      <ul class="contact-list">
        <li>+1 555 284 6190
          <svg viewBox="0 0 16 16"><path d="M3 1.5 L6 1.5 L7 5 L5.2 6.3 C6 8.2 7.8 10 9.7 10.8 L11 9 L14.5 10 L14.5 13 C14.5 14 13.7 14.5 13 14.5 C6.8 14.2 1.8 9.2 1.5 3 C1.5 2.3 2 1.5 3 1.5 Z" fill="var(--green)"/></svg>
        </li>
        <li>lv@FundTavrelle.com
          <svg viewBox="0 0 16 16"><rect x="1.5" y="3.5" width="13" height="9" fill="none" stroke="var(--green)" stroke-width="1.5"/><path d="M1.5 3.5 L8 9 L14.5 3.5" fill="none" stroke="var(--green)" stroke-width="1.5"/></svg>
        </li>
        <li>www.FundTavrelle.com
          <svg viewBox="0 0 16 16"><circle cx="8" cy="8" r="6.5" fill="none" stroke="var(--green)" stroke-width="1.3"/><ellipse cx="8" cy="8" rx="3" ry="6.5" fill="none" stroke="var(--green)" stroke-width="1.1"/><path d="M1.5 8 H14.5 M2.5 5 H13.5 M2.5 11 H13.5" stroke="var(--green)" stroke-width="1.1"/></svg>
        </li>
      </ul>
    </div>
  </section>
</main>
</body>
</html>
```